Business card design needed

I run a Beautician studio (for 7 years now)
I offer
- Velmo Body Sugaring
- Ruby Glaze
- Nails
- Facials
- Manicure
- Foot Treatment
It might not be necessary to list all those treatments?
Maybe the link to the Website is sufficient?
I leave that up to you ...
(more info on www.FernAndDewByLenka.com.au)
Velmo BodySugaring is our biggest success, It replaces waxing.
I would like to incorporate the logo into the Business Card.
We had many complaints regarding our old Business Cards as the Phone Number was to small.
On the backside, we would like a "your next Appointment" section.
Looking forward to you Design, cheers ... Lenka
Industry/Entity Type
Business
Contact Information for Business Card
Fern by Dew by Lenka
14 Korrin Sqr 3942 Ashvale
www.FernAndDewByLenka.com.au
03 9481 2267

```html
<!DOCTYPE html>
<html lang="en">
<head>
<meta charset="utf-8">
<title>Fern &amp; Dew by Lenka – Business Cards</title>
<link href="https://fonts.googleapis.com/css2?family=PT+Sans:ital,wght@0,400;0,700;1,400;1,700&family=Tinos&display=swap" rel="stylesheet">
<style>
  :root {
    --backdrop: #5e3b25;
    --card: #ffffff;
    --ink: #3a3a3a;
    --ink-soft: #555555;
    --title: #4a4a4a;
    --rule: #9a9a9a;
    --band-light: #8c8c8c;
    --band-dark: #575757;
    --brand: #3d3d3d;
    --sun: #f2a52c;
    --faint: rgba(240, 170, 60, 0.14);
  }
  * { box-sizing: border-box; margin: 0; padding: 0; }
  html, body { width: 1200px; height: 788px; overflow: hidden; }
  body {
    background: var(--backdrop);
    font-family: "PT Sans", sans-serif;
    color: var(--ink);
    position: relative;
  }
  .card {
    position: absolute;
    width: 524px;
    height: 300px;
    background: var(--card);
    border-radius: 22px;
    overflow: hidden;
    box-shadow: 0 6px 14px rgba(0,0,0,.35);
  }
  .card--front { left: 338px; top: 74px; }
  .card--back-offer { left: 54px; top: 443px; }
  .card--back-hours { left: 621px; top: 443px; }

  /* brand lockup */
  .brand { display: flex; align-items: center; gap: 8px; color: var(--brand); font-size: 17px; letter-spacing: 1px; }
  .brand__dot { width: 16px; height: 16px; border-radius: 50%; background: var(--sun); }

  /* front */
  .front__brand { position: absolute; top: 98px; left: 0; right: 0; justify-content: center; }
  .studio-name { font-size: 34px; font-weight: 400; letter-spacing: 2px; color: var(--title); text-align: center; }
  .front__name { position: absolute; top: 172px; left: 0; right: 0; }
  .front__web { position: absolute; top: 226px; left: 0; right: 0; text-align: center; font-size: 17px; color: var(--ink); }
  .contact-band { position: absolute; left: 0; bottom: 0; width: 100%; height: 32px; }
  .contact-band svg { position: absolute; inset: 0; }
  .contact-band__phone, .contact-band__address {
    position: absolute; top: 5px; color: #fff; font-size: 17px;
  }
  .contact-band__phone { left: 36px; }
  .contact-band__phone b { font-style: italic; }
  .contact-band__address { left: 293px; }

  /* back 1 */
  .offer__title { position: absolute; top: 11px; left: 0; right: 0; font-size: 27px; }
  .offer__rule { position: absolute; top: 50px; left: 0; width: 100%; border-top: 1px solid var(--rule); }
  .offer__mark {
    position: absolute; left: 140px; top: 120px; width: 230px; height: 230px;
    border-radius: 50%; background: var(--faint);
  }
  .offer__list-title, .appt__title { position: absolute; top: 69px; font-size: 19px; font-weight: 700; font-style: italic; }
  .offer__list-title { left: 29px; }
  .appt__title { left: 243px; }
  .offer__list { position: absolute; left: 30px; top: 98px; list-style: none; font-family: "Tinos", serif; font-size: 15px; color: var(--ink-soft); line-height: 20px; }
  .offer__list li::before { content: ""; display: inline-block; width: 5px; height: 5px; background: var(--ink); margin: 0 7px 3px 0; }
  .offer__divider { position: absolute; left: 206px; top: 86px; width: 3px; height: 128px; background: linear-gradient(#fff, #777 50%, #fff); }
  .appt__field { position: absolute; left: 243px; font-size: 17px; color: var(--ink); display: flex; align-items: flex-end; }
  .appt__line { display: inline-block; border-bottom: 1px solid var(--ink); height: 1px; margin-bottom: 4px; }
  .hours-small__title { position: absolute; top: 238px; left: 0; right: 0; text-align: center; font-size: 15px; font-weight: 700; font-style: italic; }
  .hours-small__row { position: absolute; top: 262px; left: 61px; font-size: 13px; word-spacing: 1px; }
  .hours-small__row span + span { margin-left: 58px; }

  /* back 2 */
  .hours__title { position: absolute; left: 32px; top: 28px; font-size: 22px; font-weight: 700; font-style: italic; letter-spacing: 1px; }
  .hours__lines { position: absolute; left: 30px; top: 60px; font-size: 19px; line-height: 24px; }
  .hours__brand { position: absolute; right: 32px; top: 78px; font-size: 15px; }
  .hours__rule { position: absolute; left: 30px; right: 30px; top: 117px; border-top: 1px solid #c8c8c8; }
  .next-appt { position: absolute; font-size: 19px; color: var(--ink); display: flex; align-items: flex-end; }
  .next-appt .appt__line { margin: 0 2px 4px; }
  .next-appt .sep { margin: 0 8px; }
  .days { position: absolute; left: 60px; top: 249px; display: flex; gap: 22px; font-size: 17px; }
  .day { display: flex; align-items: center; gap: 10px; }
  .day__box { width: 22px; height: 22px; border: 1.5px solid var(--ink); }
</style>
</head>
<body>

<!-- Front -->
<section class="card card--front" aria-label="Front of card">
  <div class="brand front__brand"><span class="brand__dot"></span>Velmo Body Sugaring</div>
  <h1 class="studio-name front__name">FERN&amp;DEW BY LENKA</h1>
  <p class="front__web">www.FernAndDewByLenka.com.au</p>
  <div class="contact-band">
    <svg width="524" height="32" viewBox="0 0 524 32">
      <polygon points="0,0 232,0 250,32 0,32" fill="var(--band-light)"/>
      <polygon points="240,0 524,0 524,32 262,32" fill="var(--band-dark)"/>
    </svg>
    <p class="contact-band__phone"><b>phone</b> 03 9481 2267</p>
    <p class="contact-band__address">14 Korrin Sqr, 3942 Ashvale</p>
  </div>
</section>

<!-- Back 1 -->
<section class="card card--back-offer" aria-label="Back of card, treatments and appointment">
  <h2 class="studio-name offer__title">FERN&amp;DEW BY LENKA</h2>
  <div class="offer__rule"></div>
  <div class="offer__mark" role="img" aria-label="Faint brand mark area"></div>
  <h3 class="offer__list-title">I offer</h3>
  <ul class="offer__list">
    <li>Velmo Body Sugaring</li>
    <li>Ruby Glaze</li>
    <li>Nails</li>
    <li>Facials</li>
    <li>Manicure</li>
    <li>Foot Treatment</li>
  </ul>
  <div class="offer__divider"></div>
  <h3 class="appt__title">An Appointment</h3>
  <p class="appt__field" style="top:110px">Name<span class="appt__line" style="width:218px"></span></p>
  <p class="appt__field" style="top:150px">Date<span class="appt__line" style="width:225px"></span></p>
  <p class="appt__field" style="top:190px">time<span class="appt__line" style="width:160px"></span>&nbsp;am / pm</p>
  <p class="hours-small__title">Hours of Operation</p>
  <p class="hours-small__row"><span>Mon. to Fri.&nbsp; 7.30am - 7.00pm</span><span>Sat. 7.30am - 12.00pm</span></p>
</section>

<!-- Back 2 -->
<section class="card card--back-hours" aria-label="Back of card, hours and next appointment">
  <h3 class="hours__title">Hours of Operation</h3>
  <p class="hours__lines">Monday to Friday -&nbsp; 7.30am - 7.00pm<br>Saturday - 7.30am - 12.00pm</p>
  <div class="brand hours__brand"><span class="brand__dot"></span>Velmo</div>
  <div class="hours__rule"></div>
  <p class="next-appt" style="left:46px; top:142px"><span class="appt__line" style="width:260px"></span>&nbsp;has an appointment</p>
  <p class="next-appt" style="left:35px; top:193px">Date :<span class="appt__line" style="width:40px"></span><span class="sep">/</span><span class="appt__line" style="width:42px"></span><span class="sep">/</span><span class="appt__line" style="width:52px"></span><span class="sep">@</span><span class="appt__line" style="width:40px"></span><span class="sep">:</span><span class="appt__line" style="width:52px"></span>am / pm</p>
  <div class="days">
    <span class="day"><span class="day__box"></span>Mon.</span>
    <span class="day"><span class="day__box"></span>Tue.</span>
    <span class="day"><span class="day__box"></span>Wed.</span>
    <span class="day"><span class="day__box"></span>Thu.</span>
    <span class="day"><span class="day__box"></span>Fri.</span>
  </div>
</section>

</body>
</html>
```